We need a new business card that reflects who we are. Professional, classy, modern, and service ori

We need a business card design for a window coverings design company in Kansas City called Bright Lane Interiors. We offer professional, modern, and high quality window covering products. We are looking to portray an image of a big, national franchise. We are a 5 location (with showrooms) business with 10 professional designers and 4 professional installers. These cards will be used with Thank you cards, given to realtors, and asked for referrals with.

Target Market(s)

Kansas City

Industry/Entity Type

Business

Contact Information for Business Card

We would like our card to look clean and simple on the front, featuring our logo and Marlow Fenwick's. Our designers' phone numbers and emails should be displayed as well as their title.

Font styles to use
Sans Serif

Colors

Designer to choose colors to be used in the design.

Requirements
Must have
• Front - Logos, name, phone number, email address
• Back - Showroom locations, social media? Appt date/time?
Nice to have
• I would like a clean and modern look (not contemporary. I like a white background, but I am open to ideas. Looking for a "National chain" look for a small business.
Should not have
• Too much busyness.

```html
<!DOCTYPE html>
<html lang="en">
<head>
<meta charset="utf-8">
<title>Bright Lane Interiors — Business Card</title>
<link rel="stylesheet" href="https://fonts.googleapis.com/css2?family=Roboto:wght@400;500&family=Roboto+Condensed:wght@400;500;700&display=swap">
<style>
  :root {
    --stage: #e9e7e4;
    --card: #f7f7f6;
    --red: #c7363f;
    --ink: #1a1a1a;
    --grey: #555555;
    --slate: #5d6672;
    --rule: #c9c9c9;
    --band: #000000;
  }
  * { box-sizing: border-box; margin: 0; padding: 0; }
  html, body { width: 1200px; height: 960px; overflow: hidden; }
  body {
    background: var(--stage);
    position: relative;
    font-family: "Roboto", Arial, sans-serif;
    color: var(--ink);
  }
  .card {
    position: absolute;
    width: 600px;
    height: 342px;
    background: var(--card);
    box-shadow: 0 2px 6px rgba(0,0,0,.25);
  }
  .card--front { left: 322px; top: 108px; }
  .card--back { left: 320px; top: 493px; height: 343px; }

  /* Front */
  .brand {
    position: absolute;
    left: 58px; top: 132px;
    width: 220px;
    text-align: center;
  }
  .brand__name {
    display: flex; align-items: center; justify-content: center; gap: 8px;
    font-weight: 500;
    font-size: 21px;
    color: var(--ink);
    white-space: nowrap;
  }
  .brand__mark { width: 14px; height: 14px; background: var(--red); flex: none; }
  .brand__tagline {
    margin-top: 6px;
    font-size: 10.5px;
    color: var(--ink);
    white-space: nowrap;
  }
  .divider {
    position: absolute;
    left: 293px; top: 117px;
    width: 1px; height: 110px;
    background: var(--rule);
  }
  .contact { position: absolute; left: 319px; top: 124px; }
  .contact__name {
    font-family: "Roboto Condensed", "Arial Narrow", sans-serif;
    font-weight: 500;
    font-size: 24px;
    color: var(--red);
    line-height: 26px;
  }
  .contact__title {
    font-weight: 500;
    font-size: 14px;
    margin-top: 2px;
    letter-spacing: .3px;
  }
  .contact__list { list-style: none; margin-top: 11px; }
  .contact__item {
    display: flex; align-items: center; gap: 9px;
    font-size: 14px; color: var(--grey);
    line-height: 19px;
  }
  .contact__icon { width: 13px; height: 13px; flex: none; fill: var(--red); }
  .web-band {
    position: absolute;
    left: 0; right: 0; top: 297px;
    height: 25px;
    background: var(--band);
    color: #fff;
    text-align: center;
    font-size: 14px;
    letter-spacing: 4.6px;
    line-height: 25px;
  }

  /* Back */
  .partner {
    position: absolute;
    left: 0; right: 0; top: 39px;
    text-align: center;
    font-family: "Roboto Condensed", "Arial Narrow", sans-serif;
    font-weight: 500;
    font-size: 16px;
    color: var(--slate);
  }
  .appointments {
    position: absolute;
    left: 82px; top: 80px;
    width: 440px;
    list-style: none;
  }
  .appointment {
    display: flex; align-items: baseline;
    height: 45px;
    color: var(--red);
    font-size: 16px;
  }
  .appointment__label { flex: none; }
  .appointment__fill {
    flex: none;
    border-bottom: 1px dotted #777;
    margin: 0 3px 0 5px;
  }
  .appointment__fill--date { width: 166px; }
  .appointment__fill--time { width: 105px; }
  .appointment__unit { font-size: 13px; margin-left: 2px; }
  .showrooms {
    position: absolute;
    left: 0; right: 0; top: 259px;
    text-align: center;
    font-family: "Roboto Condensed", "Arial Narrow", sans-serif;
  }
  .showrooms__title { font-weight: 700; font-size: 15px; color: var(--red); }
  .showrooms__list { font-size: 14px; color: var(--grey); margin-top: 2px; }
  .social { display: flex; justify-content: center; gap: 3px; margin-top: 6px; list-style: none; }
  .social__dot { width: 20px; height: 20px; border-radius: 50%; background: var(--red); }
</style>
</head>
<body>

<section class="card card--front" aria-label="Card front">
  <div class="brand">
    <div class="brand__name"><span class="brand__mark"></span>Bright Lane Interiors</div>
    <div class="brand__tagline">Blinds, Shades, Shutters, Draperies &amp; Decor</div>
  </div>
  <div class="divider"></div>
  <div class="contact">
    <div class="contact__name">DANIEL REYES</div>
    <div class="contact__title">DESIGNER</div>
    <ul class="contact__list">
      <li class="contact__item">
        <svg class="contact__icon" viewBox="0 0 24 24" aria-hidden="true"><path d="M6.6 10.8c1.4 2.8 3.8 5.1 6.6 6.6l2.2-2.2c.3-.3.7-.4 1-.2 1.1.4 2.3.6 3.6.6.6 0 1 .4 1 1V20c0 .6-.4 1-1 1C10.6 21 3 13.4 3 4c0-.6.4-1 1-1h3.5c.6 0 1 .4 1 1 0 1.3.2 2.5.6 3.6.1.3 0 .7-.2 1L6.6 10.8z"/></svg>
        913.555.0148
      </li>
      <li class="contact__item">
        <svg class="contact__icon" viewBox="0 0 24 24" aria-hidden="true"><rect x="2" y="5" width="20" height="14"/><path d="M3 6l9 7 9-7" fill="none" stroke="#fff" stroke-width="1.6"/></svg>
        info@brightlaneinteriors.com
      </li>
    </ul>
  </div>
  <div class="web-band">www.brightlaneinteriors.com</div>
</section>

<section class="card card--back" aria-label="Card back">
  <div class="partner">Marlow Fenwick Gallery</div>
  <ul class="appointments">
    <li class="appointment"><span class="appointment__label">Date :</span><span class="appointment__fill appointment__fill--date"></span><span class="appointment__label">Time :</span><span class="appointment__fill appointment__fill--time"></span><span class="appointment__unit">AM/PM</span></li>
    <li class="appointment"><span class="appointment__label">Date :</span><span class="appointment__fill appointment__fill--date"></span><span class="appointment__label">Time :</span><span class="appointment__fill appointment__fill--time"></span><span class="appointment__unit">AM/PM</span></li>
    <li class="appointment"><span class="appointment__label">Date :</span><span class="appointment__fill appointment__fill--date"></span><span class="appointment__label">Time :</span><span class="appointment__fill appointment__fill--time"></span><span class="appointment__unit">AM/PM</span></li>
    <li class="appointment"><span class="appointment__label">Date :</span><span class="appointment__fill appointment__fill--date"></span><span class="appointment__label">Time :</span><span class="appointment__fill appointment__fill--time"></span><span class="appointment__unit">AM/PM</span></li>
  </ul>
  <div class="showrooms">
    <div class="showrooms__title">SHOWROOM LOCATIONS</div>
    <div class="showrooms__list">RIVERSIDE | OAK HOLLOW | CEDAR RIDGE | NORTHGATE | WESTFIELD</div>
    <ul class="social" aria-label="Social media">
      <li class="social__dot"></li>
      <li class="social__dot"></li>
      <li class="social__dot"></li>
      <li class="social__dot"></li>
    </ul>
  </div>
</section>

</body>
</html>
```